Business card update

Opening a subsidiary of my company in the USA and need to update my logo.
Updates

Reason: Give more time to a good design.

I made a mistake on my briefing. It's only the business card. Thanks for alerting me on the mistake.

All the best

Teodoro

Target Market(s)

We are an Executive Search company and our target audience are executives in large corporations.

Industry/Entity Type

Business

Requirements
Must have
• Keep the logo. In the US the company is called Delia Brunet Executive Search.

```html
<!DOCTYPE html>
<html lang="en">
<head>
<meta charset="utf-8">
<title>Delia Brunet Executive Search – Business Card</title>
<link rel="stylesheet" href="https://fonts.googleapis.com/css2?family=Josefin+Sans:wght@300;400&display=swap">
<style>
  :root {
    --page-bg: #e8ebeb;
    --card-white: #ffffff;
    --brand-teal: #4be3b5;
    --brand-navy: #2b3a67;
    --ink-dark: #1f2a2a;
    --soft-teal: #bff3e2;
    --icon-light: #e6fbf4;
    --phone-red: #d0282c;
  }
  * { box-sizing: border-box; margin: 0; padding: 0; }
  html, body { width: 1200px; height: 741px; overflow: hidden; }
  body {
    background: var(--page-bg);
    font-family: "Josefin Sans", sans-serif;
    position: relative;
  }
  .business-card {
    position: absolute;
    left: 75px; top: 66px;
    width: 1050px; height: 609px;
    background: var(--card-white);
    overflow: hidden;
  }
  .card-header {
    position: absolute; left: 0; top: 0; width: 100%; height: 178px;
  }
  .brand-rule {
    position: absolute; left: 245px; top: 82px; width: 560px; height: 2px;
    background: var(--brand-teal);
  }
  .brand-name {
    position: absolute; left: 0; top: 98px; width: 100%;
    text-align: center;
    font-weight: 400; font-size: 36px; letter-spacing: 7px;
    color: var(--brand-navy);
  }
  .contact-band {
    position: absolute; left: 0; top: 178px; width: 100%; height: 278px;
    background: var(--brand-teal);
  }
  .person-name {
    position: absolute; left: 56px; top: 92px;
    font-weight: 400; font-size: 42px; color: var(--card-white);
  }
  .person-phone {
    position: absolute; left: 56px; top: 153px;
    display: flex; align-items: center; gap: 14px;
    font-size: 34px; color: var(--ink-dark);
  }
  .person-phone svg { width: 26px; height: 28px; }
  .contact-list {
    position: absolute; left: 548px; top: 96px; list-style: none;
  }
  .contact-item {
    display: flex; align-items: center; gap: 28px;
    height: 52px;
    font-size: 24px; font-weight: 300; color: var(--ink-dark);
  }
  .contact-item svg { width: 36px; height: 28px; }
  .card-footer {
    position: absolute; left: 0; top: 456px; width: 100%; height: 153px;
  }
  .company-line {
    position: absolute; left: 0; top: 30px; width: 100%;
    display: flex; align-items: center; gap: 10px;
  }
  .company-line .rule { flex: 1; height: 2px; background: var(--soft-teal); }
  .company-name {
    font-weight: 300; font-size: 38px; letter-spacing: 1.5px;
    color: var(--soft-teal); white-space: nowrap;
  }
  .company-address {
    position: absolute; left: 0; top: 92px; width: 100%;
    text-align: center; font-weight: 300; font-size: 24px;
    color: var(--soft-teal);
  }
</style>
</head>
<body>
  <article class="business-card">
    <header class="card-header">
      <div class="brand-rule"></div>
      <div class="brand-name">DELIA BRUNET</div>
    </header>

    <section class="contact-band">
      <h1 class="person-name">Teodoro S. Brunet</h1>
      <p class="person-phone">
        <svg viewBox="0 0 24 24" aria-hidden="true">
          <path fill="var(--phone-red)" d="M6.6 2.5c.6-.4 1.4-.2 1.8.4l2 3.3c.4.6.2 1.4-.4 1.8l-1.6 1c.8 2.1 2.4 4 4.4 5.2l1.1-1.5c.4-.6 1.2-.8 1.8-.4l3.2 2.1c.6.4.8 1.2.4 1.8l-1.3 2.1c-.6 1-1.9 1.5-3 1.1C9 17.2 5 12.6 3.5 7c-.3-1.1.2-2.3 1.2-2.9z"/>
        </svg>
        305 555-0147
      </p>
      <ul class="contact-list">
        <li class="contact-item">
          <svg viewBox="0 0 36 28" aria-hidden="true">
            <rect x="2" y="4" width="32" height="20" rx="2" fill="var(--icon-light)"/>
            <path d="M3 5l15 11L33 5" fill="none" stroke="var(--brand-teal)" stroke-width="2"/>
          </svg>
          www.dbexecutivesearch.com
        </li>
        <li class="contact-item">
          <svg viewBox="0 0 36 28" aria-hidden="true">
            <circle cx="18" cy="14" r="12" fill="var(--icon-light)"/>
            <path d="M12 8c3 1 4 3 3 5s1 4 3 4M22 6c-1 3 1 5 4 6" fill="none" stroke="var(--brand-teal)" stroke-width="2"/>
          </svg>
          tbrunet@dbexecutivesearch.com
        </li>
      </ul>
    </section>

    <footer class="card-footer">
      <div class="company-line">
        <span class="rule"></span>
        <span class="company-name">Delia Brunet Executive Search</span>
        <span class="rule"></span>
      </div>
      <p class="company-address">4820 Harbor Point Blvd Suite 310, Coral Bay, FL 33190</p>
    </footer>
  </article>
</body>
</html>
```